Business Card front and back

I am looking for business card design. I really really like the design file I uploaded named 627788_19250069_3478263_85f427ee_image

Target Market(s)

Corporate Fitness High end Private country club

Industry/Entity Type

Fitness Industry

Contact Information for Business Card

The last image I like as an example I uploaded a bunch of my logos. The file labeled "the signature" is my business card information for you to use

Colors
0054AA
0677BA
7BADD7
CADEEF
E8F1F8

Requirements
Must have
• E-mail sigThe file I uploaded labeled "627788_19250069_3478263_85f427ee_image" with all the plus signs on the back if those could be the logo symbol I uploaded labeled "1 back.png"

```html
<!DOCTYPE html>
<html lang="en">
<head>
<meta charset="utf-8">
<title>Peak Form Studio – Business Card</title>
<link rel="stylesheet" href="https://fonts.googleapis.com/css2?family=Exo+2:ital,wght@0,500;0,700;0,800;1,600;1,800&display=swap">
<style>
  :root {
    --stage: #2c2d2f;
    --card-white: #ffffff;
    --soft-grey: #e4e4e4;
    --ink: #2a2a2c;
    --blue: #4479c0;
    --blue-deep: #0054aa;
    --blue-pale: #7badd7;
    --strip: #2b2b2d;
    --photo-dark: #1e1e1e;
    --photo-mid: #4a4642;
  }
  * { box-sizing: border-box; margin: 0; padding: 0; }
  html, body { width: 1200px; height: 866px; overflow: hidden; }
  body {
    background: var(--stage);
    font-family: "Exo 2", sans-serif;
    display: flex; flex-direction: column; align-items: center; justify-content: center;
    gap: 22px;
  }
  .card { position: relative; width: 700px; height: 400px; overflow: hidden; }

  /* front */
  .card-front { background: var(--card-white); }
  .front-panel {
    position: absolute; left: 0; top: 40px; width: 430px; height: 280px;
    background: var(--soft-grey); border-radius: 0 140px 140px 0;
  }
  .brand {
    position: absolute; left: 56px; top: 86px;
    display: flex; align-items: center; gap: 12px;
    font-weight: 800; font-size: 30px; letter-spacing: 1px; color: var(--ink);
    text-transform: uppercase;
  }
  .brand-square { width: 22px; height: 22px; background: var(--blue); }
  .contact { position: absolute; left: 58px; top: 160px; list-style: none; }
  .contact li {
    display: flex; align-items: center; gap: 10px;
    font-weight: 500; font-size: 17px; color: var(--ink); line-height: 30px;
  }
  .contact svg { width: 16px; height: 16px; fill: var(--blue); flex: none; }
  .photo-frame {
    position: absolute; left: 438px; top: 78px; width: 200px; height: 170px;
    border: 2px solid var(--blue);
  }
  .photo {
    position: absolute; left: 446px; top: 86px; width: 184px; height: 154px;
    background: radial-gradient(circle at 50% 55%, var(--photo-mid), var(--photo-dark) 70%);
  }
  .person { position: absolute; right: 60px; top: 262px; text-align: right; }
  .person-name {
    font-weight: 800; font-size: 28px; letter-spacing: 1px; color: var(--ink);
    text-transform: uppercase; font-style: italic;
  }
  .person-name .surname { color: var(--blue); }
  .person-role { font-weight: 600; font-style: italic; font-size: 19px; color: var(--ink); letter-spacing: 1px; }
  .accent-line { position: absolute; left: 0; bottom: 44px; width: 260px; height: 5px; background: var(--blue); }
  .web-strip { position: absolute; left: 230px; bottom: 0; width: 470px; height: 48px; }
  .web-strip svg { position: absolute; inset: 0; }
  .website {
    position: absolute; right: 60px; bottom: 12px;
    font-weight: 600; font-style: italic; font-size: 18px; letter-spacing: 1px; color: #d8d8d8;
  }
  .website .tld { color: var(--blue-pale); }

  /* back */
  .card-back { background: var(--blue); }
  .back-texture {
    position: absolute; inset: 0;
    background: linear-gradient(135deg, #4a80c8 0%, var(--blue) 50%, #3c70b6 100%);
  }
  .back-brand {
    position: absolute; right: 70px; bottom: 70px;
    display: flex; align-items: center; gap: 12px;
    font-weight: 800; font-size: 26px; letter-spacing: 1px; color: var(--card-white);
    text-transform: uppercase;
  }
  .back-brand .brand-square { background: var(--card-white); }
</style>
</head>
<body>

  <section class="card card-front" aria-label="Business card front">
    <div class="front-panel"></div>
    <div class="brand"><span class="brand-square"></span>Peak Form Studio</div>
    <ul class="contact">
      <li>
        <svg viewBox="0 0 24 24" aria-hidden="true"><path d="M6.6 10.8a15.1 15.1 0 0 0 6.6 6.6l2.2-2.2a1 1 0 0 1 1-.25 11.4 11.4 0 0 0 3.6.57 1 1 0 0 1 1 1V20a1 1 0 0 1-1 1A17 17 0 0 1 3 4a1 1 0 0 1 1-1h3.5a1 1 0 0 1 1 1c0 1.25.2 2.45.57 3.6a1 1 0 0 1-.25 1z"/></svg>
        555-010-4821
      </li>
      <li>
        <svg viewBox="0 0 24 24" aria-hidden="true"><path d="M2 5h20v14H2z M2 5l10 8 10-8" fill="none" stroke="#4479c0" stroke-width="2.4"/></svg>
        dana@peakformstudio.co
      </li>
      <li>
        <svg viewBox="0 0 24 24" aria-hidden="true"><path d="M12 2a7 7 0 0 0-7 7c0 5.2 7 13 7 13s7-7.8 7-13a7 7 0 0 0-7-7zm0 9.5A2.5 2.5 0 1 1 12 6.5a2.5 2.5 0 0 1 0 5z"/></svg>
        OR.WA.ID.MT.WY
      </li>
    </ul>
    <div class="photo-frame"></div>
    <div class="photo" role="img" aria-label="Portrait photo of the consultant"></div>
    <div class="person">
      <p class="person-name">Dana <span class="surname">Morrow</span></p>
      <p class="person-role">Consultant</p>
    </div>
    <div class="accent-line"></div>
    <div class="web-strip">
      <svg viewBox="0 0 470 48" preserveAspectRatio="none" aria-hidden="true">
        <path d="M0 48 C 20 48, 20 0, 50 0 H470 V48 Z" fill="#2b2b2d"/>
      </svg>
      <p class="website">www.peakformstudio<span class="tld">.co</span></p>
    </div>
  </section>

  <section class="card card-back" aria-label="Business card back">
    <div class="back-texture" role="img" aria-label="Embossed repeating brand pattern on blue"></div>
    <div class="back-brand"><span class="brand-square"></span>Peak Form Studio</div>
  </section>

</body>
</html>
```